Herbal Apothecary Rebrand

I am in the process of merging two companies Fern Hollow Oils and Under Willow Apothecary. I am dissolving Fern Hollow Oils (FHO) and need to blend a few of the products into the Under Willow Apothecary (UWA) line. These blended products will take on a fresh new look. This is where I need some help. I have a few ideas but need some creative genius to bring them together.
The following products need to be merged and once a logo is agreed upon I will be working with this designer with further pay to create the following:
~ body oils (labels and packaging) **existing product shown in image A-1
~ plant bath medicines (labels and packaging) **a new product with the bottle and packaging shown in images attached
~ facial serum (labels and packaging - the packaging will be the same cardboard boxes used for the body oils) **existing product shown in
image A-2
~ teas (labeling) **a new product - packaging sample pics attached
~ as well as having the ability to carry over into the creation of 40 different essential oil containers. ** An idea I have is shown in image C-1.
Ideas...
I prefer distinct lines, square designs vs circular or curvy. I prefer clean and clear vs busy.
I like the layout shown in images A-1 & A-2 and could see moving forward with a very similar style without the indigenous logo. I would like to see what it looks like to have the UWA logo (building with trees) in place of the indigenous logo. ** I am open to reworking the UWA logo to make it a bit more vertical in size vs being quite small and horizontal. This could include revising or recreating the building and trees altogether.
I like the speckled background (shown in image B-1), it gives the sense that it is aged and goes with the Apothecary theme, however I'm not completely attached to it.
I like the off white labels that I currently have for the BODY OILS and the SERUM and I am leaning towards this as the colour for the new blended line. I would also be open to seeing a lighter version of the turquoise.
This is just an idea that I have however I am open to something completely new. What is important is that it blends nicely with the current line of products available at UWA (the entire line can be seen online). There is a good chance that I will be merging the products over to the new and improved design as we move through the older packaging.
Notes on Plant Bath labels:
**If working from the current layout of the Body Oil labels this can be used as an example to create a template
~ The top will have the new or reworked logo (with or without the company name depending on space available)
~ First line for each bottle will have a name eg: NETTLE + ROSE
~ Second line will be the purpose of the medicine eg: HEART OPENING
~ The next line will read: PLANT BATH
~Then space for a little blurb eg: BRINGING BALANCE TO THE EMOTIONAL AND ENERGETIC HEALTH OF THE HEART.
~ The size of the bottle will read 400 ML but in a vertical direction on the bottle
Notes on Tea labels:
The teas have not been created yet but I'm looking for some ideas that follow in the same design as the Plant Bath labels so the following can be used as an example:
~ Name; TULSI + ROSE
~ The purpose: ELEVATED HEART
~ The bottom will read: LOOSE TEA
~ Blurb about the benefits: A TRANSFORMATIONAL CREATION OF WARM NOTES WITH DEEP WOODY UNDERTONES. THIS ANYTIME TEA IS AS PLEASING IN THE HEALTH BENEFITS AS IT IS TO THE TASTE.
~ Include the size: 100g
**I maxed out in pictures so I wasn't able to add more inspiration pics but I also quite like the brook & meadow tea line (shows up in a google search) as its clean and clear. The difference being I won't be printing directly on the packaging, it will need to be a label.
Logo Text
I would like to see if we can incorporate the name UNDER WILLOW APOTHECARY however this might make it too busy. Perhaps smaller lettering for "under willow" and larger for "APOTHECARY". It also might be the case that adding this on the front makes things look too busy. I'm open to creative suggestions.

```html
<!DOCTYPE html>
<html lang="en">
<head>
<meta charset="utf-8">
<title>Under Willow Apothecary – Label Range</title>
<link href="https://fonts.googleapis.com/css2?family=Oswald:wght@300;400&display=swap" rel="stylesheet">
<style>
  :root {
    --ink: #6e2a1d;
    --paper: #efeeea;
    --canvas: #ffffff;
    --art: #b88f84;
  }
  * { margin: 0; padding: 0; box-sizing: border-box; }
  html, body { width: 1200px; height: 848px; overflow: hidden; background: var(--canvas); }
  body { position: relative; font-family: "Oswald", sans-serif; color: var(--ink); }

  .label { position: absolute; background: var(--paper); width: 524px; height: 382px; }
  .label > * { position: absolute; }

  .label--oil   { left: 58px;  top: 38px; }
  .label--bath  { left: 618px; top: 38px; }
  .label--tea   { left: 58px;  top: 424px; }

  /* side copy, reading bottom to top */
  .side-copy {
    writing-mode: vertical-rl; transform: rotate(180deg);
    font-weight: 300; font-size: 9.6px; line-height: 11.4px; letter-spacing: .2px;
    text-transform: uppercase;
  }
  .side-copy b { font-weight: 400; }
  .label .usage { left: 26px; top: 30px; height: 350px; width: 36px; }
  .label .ingredients { left: 70px; top: 30px; height: 350px; width: 14px; }

  .brand { left: 147px; top: 30px; width: 230px; text-align: center; font-weight: 400; line-height: 1; }
  .brand__small { display: block; font-size: 11px; letter-spacing: 3px; }
  .brand__large { display: block; font-size: 20px; letter-spacing: 1.5px; margin-top: 6px; }

  .emblem { left: 152px; top: 90px; width: 205px; height: 72px; background: var(--art); opacity: .55; }

  .product-name { left: 147px; width: 230px; bottom: 166px; font-size: 28px; font-weight: 400; line-height: 1; letter-spacing: .5px; }
  .label--bath .product-name, .label--tea .product-name { font-size: 37px; letter-spacing: 1.5px; }

  .rule { left: 147px; width: 230px; height: 1.5px; background: var(--ink); }
  .rule--1 { top: 224px; } .rule--2 { top: 260px; } .rule--3 { top: 287px; } .rule--4 { top: 354px; }

  .product-type { left: 147px; top: 229px; font-size: 23px; font-weight: 300; letter-spacing: 2.6px; line-height: 28px; }
  .tagline { left: 147px; top: 266px; font-size: 13px; font-weight: 300; letter-spacing: .4px; line-height: 16px; }
  .blurb { left: 147px; bottom: 34px; width: 180px; font-size: 13px; font-weight: 300; letter-spacing: .3px; line-height: 16px; }
  .divider { left: 325px; top: 297px; width: 1.5px; height: 50px; background: var(--ink); }
  .volume { left: 338px; top: 297px; height: 50px; writing-mode: vertical-rl; transform: rotate(180deg);
            font-size: 16px; font-weight: 400; letter-spacing: 1.5px; text-align: center; }

  .info-panel { left: 423px; top: 34px; width: 76px; height: 320px; border: 1px solid var(--ink); }
  .web { left: 478px; top: 34px; height: 320px; writing-mode: vertical-rl; transform: rotate(180deg);
         font-size: 9.5px; font-weight: 300; letter-spacing: .6px; text-align: center; }

  /* serum label */
  .label--serum { left: 618px; top: 508px; width: 414px; height: 254px; }
  .label--serum .usage { left: 30px; top: 30px; height: 205px; width: 24px; font-size: 8.6px; line-height: 10.5px; }
  .label--serum .ingredients { left: 62px; top: 30px; height: 205px; width: 24px; font-size: 8.6px; line-height: 10.5px; }
  .label--serum .brand { left: 118px; top: 32px; width: 150px; }
  .label--serum .brand__small { font-size: 8px; letter-spacing: 2.4px; }
  .label--serum .brand__large { font-size: 15px; letter-spacing: 1px; margin-top: 4px; }
  .label--serum .product-name { left: 118px; width: 182px; top: 95px; bottom: auto; font-size: 24px; letter-spacing: .6px; }
  .label--serum .rule { left: 118px; width: 180px; }
  .label--serum .rule--1 { top: 135px; } .label--serum .rule--2 { top: 180px; } .label--serum .rule--4 { top: 232px; }
  .label--serum .product-type { left: 118px; top: 147px; font-size: 20px; letter-spacing: 1.8px; }
  .label--serum .blurb { left: 118px; bottom: auto; top: 202px; width: 120px; font-size: 9.6px; line-height: 11.5px; }
  .label--serum .divider { left: 255px; top: 196px; height: 30px; }
  .label--serum .volume { left: 272px; top: 196px; height: 34px; font-size: 12px; }
  .label--serum .info-panel { left: 322px; top: 22px; width: 77px; height: 218px; }
  .label--serum .web { left: 369px; top: 22px; height: 218px; font-size: 8px; }
</style>
</head>
<body>

<section class="label label--oil">
  <p class="side-copy usage"><b>Suggested use:</b> warm oil if desired. Apply to the full body after bathing. Massage in motions toward the heart until the oil is mostly absorbed. Can also be added to bath water.</p>
  <p class="side-copy ingredients"><b>Ingredients:</b> sunflower oil, orange, cardamom, cypress, ginger organic.</p>
  <div class="brand"><span class="brand__small">UNDER WILLOW</span><span class="brand__large">APOTHECARY</span></div>
  <div class="emblem" role="img" aria-label="Illustration of a cabin among trees"></div>
  <h2 class="product-name">CARDAMON + CYPRESS</h2>
  <div class="rule rule--1"></div>
  <p class="product-type">WARMING BODY OIL</p>
  <div class="rule rule--2"></div>
  <p class="tagline">ORGANIC BOTANICALS</p>
  <div class="rule rule--3"></div>
  <p class="blurb">REVITALIZING AND STIMULATING FOR A RENEWED SENSE OF SPIRIT</p>
  <div class="divider"></div>
  <p class="volume">100ML</p>
  <div class="rule rule--4"></div>
  <div class="info-panel"></div>
  <p class="web">underwillowapothecary.com</p>
</section>

<section class="label label--bath">
  <p class="side-copy usage"><b>Suggested use:</b> warm oil if desired. Apply to the full body after bathing. Massage in motions toward the heart until the oil is mostly absorbed. Can also be added to bath water.</p>
  <p class="side-copy ingredients"><b>Ingredients:</b> sunflower oil, orange, cardamom, cypress, ginger organic.</p>
  <div class="brand"><span class="brand__small">UNDER WILLOW</span><span class="brand__large">APOTHECARY</span></div>
  <div class="emblem" role="img" aria-label="Illustration of a cabin among trees"></div>
  <h2 class="product-name">NETTLE + ROSE</h2>
  <div class="rule rule--1"></div>
  <p class="product-type">PLANT BATH</p>
  <div class="rule rule--2"></div>
  <p class="tagline">ORGANIC BOTANICALS</p>
  <div class="rule rule--3"></div>
  <p class="blurb">BRINGING BALANCE TO THE EMOTIONAL AND ENERGETIC HEALTH OF THE HEART</p>
  <div class="divider"></div>
  <p class="volume">400ML</p>
  <div class="rule rule--4"></div>
  <div class="info-panel"></div>
  <p class="web">underwillowapothecary.com</p>
</section>

<section class="label label--tea">
  <p class="side-copy usage"><b>Suggested use:</b> warm oil if desired. Apply to the full body after bathing. Massage in motions toward the heart until the oil is mostly absorbed. Can also be added to bath water.</p>
  <p class="side-copy ingredients"><b>Ingredients:</b> sunflower oil, orange, cardamom, cypress, ginger organic.</p>
  <div class="brand"><span class="brand__small">UNDER WILLOW</span><span class="brand__large">APOTHECARY</span></div>
  <div class="emblem" role="img" aria-label="Illustration of a cabin among trees"></div>
  <h2 class="product-name">TULSI + ROSE</h2>
  <div class="rule rule--1"></div>
  <p class="product-type">LOOSE TEA</p>
  <div class="rule rule--2"></div>
  <p class="tagline">ORGANIC BOTANICALS</p>
  <div class="rule rule--3"></div>
  <p class="blurb" style="width:190px">A TRANSFORMATIONAL CREATION OF WARM NOTES WITH DEEP WOODY UNDERTONES.</p>
  <div class="divider" style="left:340px"></div>
  <p class="volume" style="left:352px">100g</p>
  <div class="rule rule--4"></div>
  <div class="info-panel"></div>
  <p class="web">underwillowapothecary.com</p>
</section>

<section class="label label--serum">
  <p class="side-copy usage">Suggested use: warm oil if desired. Apply to the full body after bathing.</p>
  <p class="side-copy ingredients">Ingredients: sunflower oil, orange, cardamom, cypress, ginger organic.</p>
  <div class="brand"><span class="brand__small">UNDER WILLOW</span><span class="brand__large">APOTHECARY</span></div>
  <h2 class="product-name">CAMOMILE + ROSE</h2>
  <div class="rule rule--1"></div>
  <p class="product-type">BALANCING SERUM</p>
  <div class="rule rule--2"></div>
  <p class="blurb">BOTANICALS TO TAME THE WILD HUNTRESS</p>
  <div class="divider"></div>
  <p class="volume">35 ML</p>
  <div class="rule rule--4"></div>
  <div class="info-panel"></div>
  <p class="web">underwillowapothecary.com</p>
</section>

</body>
</html>
```